Brochure to attract insurance agents to outsource their bookkeeping

I need a brochure to handout at trade shows. Company name is Broker Office Ledger & Records. We go by BOLR. We provide bookkeeping services. I have attached the current brochure, which is a few years old, stale and outdated (not created on Pixmundo). I have also attached our graphic identity manual which show fonts/colors as well as our logo in 3 styles

Target Market(s)

Insurance Agents needing bookkeeping services

Industry/Entity Type

Accounting

Other font styles liked:
• See the graphic id manual

Colors
00AB8E
00BBA5
67D7C9
C6EFE9
E9F9F6

Requirements
Must have
• Services noted (see current brochure), contact info, reference to Vantrel Core

```html
<!DOCTYPE html>
<html lang="en">
<head>
<meta charset="utf-8">
<title>BOLR Brochure</title>
<link href="https://fonts.googleapis.com/css2?family=Montserrat:ital,wght@0,400;0,500;0,600;0,700;0,800;1,400;1,600&display=swap" rel="stylesheet">
<style>
:root{
  --teal:#00AB8E;
  --teal-2:#00BBA5;
  --teal-3:#67D7C9;
  --mint:#C6EFE9;
  --mint-2:#E9F9F6;
  --panel:#b3e6dd;
  --table-dark:#0b5f55;
  --gray:#6a6a6a;
  --gray-dark:#4e4e4e;
  --ink:#1f2a2a;
  --white:#ffffff;
  --stage-bg:#e4e4e6;
}
*{box-sizing:border-box;margin:0;padding:0}
html,body{width:1200px;height:792px;overflow:hidden;background:var(--stage-bg);font-family:'Montserrat',Arial,sans-serif}
.stage{position:absolute;left:292px;top:2px;width:1232px;height:1576px;transform:scale(.5);transform-origin:0 0}
.spread{position:relative;width:1232px;height:778px;overflow:hidden;background:var(--white)}
.spread + .spread{margin-top:20px;background:var(--teal)}
.spread svg.bg{position:absolute;inset:0}
.abs{position:absolute}

/* inside spread */
.banner{left:0;top:33px;width:380px;height:52px;background:var(--gray);clip-path:polygon(0 0,100% 0,94% 100%,0 100%);color:#fff;font-size:18px;font-weight:600;padding:14px 0 0 22px;white-space:nowrap}
.intro{left:40px;top:105px;width:250px;font-size:10.5px;font-weight:500;line-height:15px;color:var(--ink);text-transform:uppercase}
.bullets{list-style:none}
.bullets li{position:relative;padding-left:16px;font-size:12.5px;line-height:18px;margin-bottom:18px}
.bullets li::before{content:"";position:absolute;left:0;top:6px;width:5px;height:5px;background:currentColor}
.col-1{left:30px;top:232px;width:245px;color:var(--ink)}
.col-1 li::before{background:var(--teal)}
.col-2{left:340px;top:400px;width:270px;color:#fff}
.brand{color:#fff;font-weight:800;text-align:right}
.brand .name{font-size:60px;letter-spacing:-1px;line-height:58px}
.brand .full{font-size:12.5px;font-weight:800;line-height:16px;text-transform:uppercase}
.brand-inside{left:430px;top:280px;width:170px}
.h-why{left:647px;top:57px;color:#fff;font-size:22px;font-weight:500;line-height:23px}
.why-body{left:647px;top:110px;width:262px;color:#fff;font-size:9.6px;line-height:15.3px;text-align:justify}
.why-body p{margin-bottom:14px}
.h-fees{left:938px;top:200px;color:#fff;font-size:24px;font-weight:500;line-height:22px}
.h-fees b{font-weight:600}
.fees-note{left:938px;top:290px;width:270px;color:#fff;font-size:9.6px;font-style:italic;font-weight:600;line-height:15.5px}
.fees{left:960px;top:398px;width:222px;border:3px solid #fff;background:#fff;border-collapse:collapse;font-size:13px}
.fees th{background:var(--gray);color:#fff;font-weight:400;text-align:left;padding:4px 10px 6px;line-height:14px;vertical-align:top}
.fees td{padding:2px 10px;line-height:16px;color:var(--ink)}
.fees tr.dark td{background:var(--table-dark);color:#fff}
.fees tr.gap td{padding:0;height:6px;background:#fff}
.fees-more{left:938px;top:628px;width:270px;color:#fff;font-size:11px;line-height:13px}
.contact{right:24px;text-align:right;color:#fff}
.contact .phone{font-size:19px;font-weight:600}
.contact .web{font-size:14px}
.contact .tm{font-size:6.5px}
.contact-inside{top:710px}

/* outside spread */
.person{color:var(--gray-dark);font-size:12px;line-height:13px;text-align:center}
.person b{font-size:13px;font-weight:600;display:block}
.person.light{color:#fff}
.about{left:25px;top:252px;width:265px;color:#fff;font-size:12.5px;line-height:20px}
.mission{left:0;top:342px;width:285px;background:var(--panel);color:var(--ink);font-size:12.5px;font-weight:600;line-height:19px;padding:8px 10px 10px 25px}
.mission::after{content:"";position:absolute;right:10px;bottom:-10px;border:6px solid transparent;border-top:6px solid var(--panel);border-right-color:var(--panel)}
.bio{left:25px;top:476px;width:270px;color:#fff;font-size:11.4px;line-height:15.6px}
.bio p{margin-bottom:13px}
.partner{left:340px;top:438px;width:260px;color:#fff;font-size:24px;font-style:italic;line-height:27px;font-weight:400}
.brand-box{left:348px;top:520px;width:202px;height:182px;background:var(--panel);padding:30px 14px 0;text-align:center;color:var(--teal)}
.brand-box .name{font-size:50px;font-weight:800;letter-spacing:-1px;line-height:52px}
.brand-box .full{font-size:11px;font-weight:800;line-height:14px;text-transform:uppercase;margin-top:4px}
.brand-box .addr{color:var(--gray-dark);font-size:13px;line-height:16px;margin-top:12px}
.premier{left:652px;top:83px;width:245px;color:#fff;font-size:17px;font-weight:700;line-height:21.5px;text-transform:uppercase}
.services{left:647px;top:196px;width:245px;height:560px}
.service{position:absolute;left:14px;display:flex;align-items:center;gap:14px;color:#505a5a;font-size:13.5px;line-height:14px}
.service svg{flex:none}
.web-small{left:647px;top:720px;width:245px;text-align:center;color:var(--ink);font-size:9px}
.expert{right:22px;top:270px;width:300px;text-align:right;color:#fff;font-size:27px;font-weight:800;line-height:37px;text-transform:uppercase}
.expert-sub{right:22px;top:440px;width:160px;text-align:right;color:#fff;font-size:9px;line-height:12px}
.brand-back{left:960px;top:550px;width:210px;text-align:center;color:var(--teal)}
.brand-back .name{font-size:60px;font-weight:800;letter-spacing:-1px;line-height:60px}
.brand-back .full{font-size:13px;font-weight:800;line-height:16px;text-transform:uppercase}
.brand-back .web{color:var(--ink);font-size:10.5px;margin-top:10px}
.brand-back .phone{color:var(--ink);font-size:20px;font-weight:600;margin-top:14px}
</style>
</head>
<body>
<main class="stage">

  <section class="spread spread-inside">
    <svg class="bg" viewBox="0 0 1232 778" width="1232" height="778">
      <defs>
        <linearGradient id="gWoman" x1="0" y1="0" x2="1" y2="1">
          <stop offset="0" stop-color="#f2b63a"/><stop offset=".55" stop-color="#e9a06a"/><stop offset="1" stop-color="#6f9ab8"/>
        </linearGradient>
        <linearGradient id="gDesk" x1="0" y1="0" x2="1" y2="1">
          <stop offset="0" stop-color="#9a9a9a"/><stop offset="1" stop-color="#dedede"/>
        </linearGradient>
      </defs>
      <path d="M312,0 H612 L610,150 Q600,240 540,262 L318,262 Q308,180 330,110 Z" fill="url(#gWoman)" role="img" aria-label="Photo of a smiling agency staff member"/>
      <path d="M612,0 H1232 V778 H205 L285,672 L285,440 L440,262 L540,262 Q605,230 612,150 Z" fill="var(--teal)"/>
      <path d="M205,778 H285 L520,470 H460 Z" fill="var(--teal-3)" opacity=".55"/>
      <rect x="150" y="560" width="135" height="175" fill="var(--panel)"/>
      <path d="M997,0 H1232 V175 Q1170,160 1120,190 Q1060,230 997,215 Z" fill="url(#gDesk)" role="img" aria-label="Photo of hands working on a laptop and calculator"/>
      <path d="M870,778 Q990,700 1110,682 Q1190,668 1232,640 V778 Z" fill="var(--gray)"/>
    </svg>

    <div class="abs banner">How outsourcing to BOLR works</div>
    <p class="abs intro">We access your Vantrel Core online database in the same manner as agency staff. You provide the login credentials. Below is a high-level overview of the process.<br>A detailed operational workflow is provided to each client agency.</p>

    <ul class="abs bullets col-1">
      <li>Agency staff routes accounting documents to BOLR through Vantrel Core</li>
      <li>Agency staff makes bank deposite of paper checks and cash, routing documentation to BOLR to record in Vantrel Core. BOLR records EFT transactions from the bank records.</li>
      <li>BOLR pays your vendors and insurance companies/brokers via Vantrel Core checks that you print, or via your bank's bill pay system, or via ACH. Agencies may choose the method.</li>
      <li>BOLR reconciles Agency staff in voicing on all agency bill transactions with insurance company/broker records at time of payment. We work with your staff on discrepancies.</li>
    </ul>

    <div class="abs brand brand-inside">
      <div class="name">BOLR</div>
      <div class="full">Broker Office<br>Ledger &amp; Records</div>
    </div>

    <ul class="abs bullets col-2">
      <li>BOLR records all direct bill commission at the time commission is received; this includes downloads, imports, and manual entry. You provide the commission statements or provide online access for BOLR to obtain.</li>
      <li>BOLR reconciles all bank accounts in Vantrel Core with your bank's data at least twice per week. You provide the login credentials.</li>
      <li>BOLR sends financial statements to Agency Principals each month. We encourage review and discussion.</li>
    </ul>

    <h2 class="abs h-why">Why outsourcing to<br>BOLR works</h2>
    <div class="abs why-body">
      <p>Our Staff is Educated in Accounting &amp; Trained in Vantrel Core. The BOLR staff consists of Accountants, Bookkeepers, and Clerks. All are well trained in their responsibilities for Vantrel Core accounting. Accountants have earned bachelor's degrees in accounting and have several years of Vantrel Core experience; Bookkeepers have earned associate degree credits in accounting or have significant bookkeeping experience; Clerks have a variety of experiences and education levels, many are in school for accounting, all are detail oriented numbers people. Agency clients get the benefit of a full BOLR team.</p>
      <p>Our Work goes through a Quality Control Process. BOLR has a proprietary system of checks and balances to ensure client's financial statements are complete and accurate. All financial statement packages are prepared by our bookkeeping staff and reviewed by a staff accountant before presentation to the client. Agency principals are encouraged to discuss their statements with their BOLR accountant. Our goal is for our clients to understand their financial data, empowering them to make sound financial decisions.</p>
      <p>We always have a Backup. When your BOLR Bookkeeper is out of the office a backup is always available. Should your BOLR Bookkeeper leave BOLR, another trained staff member will be available.</p>
      <p>We Implement Controls for Data Security. All computer equipment is owned by BOLR. PCs and routers are regularly updated to stay current with technology. All are continuously monitored for System updates and virus/malware by an independent IT firm. Dual authentication is required for remote access to our PCs. Documents are shared within Vantrel Core or through a secure document sharing platform, VaultShare.</p>
    </div>

    <h2 class="abs h-fees">How the<br><b>BOLR FEES</b> are<br>structured</h2>
    <p class="abs fees-note">Fees are a flat monthly rate based on annual policy commission revenue. The table below lists sample rates for our full-service offerings at different revenue volumes for an Agency with a typical mix of business and complexity. Fees assume compliance with our standard operating workflows.</p>
    <table class="abs fees">
      <tr><th>Annual<br>Commission<br>Revenue</th><th>Monthly<br>Service<br>Fee</th></tr>
      <tr class="gap"><td></td><td></td></tr>
      <tr class="dark"><td>&lt;$300,000</td><td>$600</td></tr>
      <tr><td>$700,000</td><td>$1,400</td></tr>
      <tr class="dark"><td>$1,000,000</td><td>$2,000</td></tr>
      <tr><td>$1,500,000</td><td>$2,500</td></tr>
      <tr class="dark"><td>$2,000,000</td><td>$3,000</td></tr>
      <tr><td>$2,500,000</td><td>$3,500</td></tr>
      <tr class="dark"><td>$3,000,000</td><td>$4,500</td></tr>
      <tr class="gap"><td></td><td></td></tr>
    </table>
    <p class="abs fees-more">We can provide services for larger agencies, typically supplementing in-house staff.</p>

    <div class="abs contact contact-inside">
      <div class="phone">&#9990; 555.014.2290</div>
      <div class="web">www.BrokerLedgerRecords.com</div>
      <div class="tm">Vantrel Core is a registered trademark of Vantrel Systems, Inc.</div>
    </div>
  </section>

  <section class="spread spread-outside">
    <svg class="bg" viewBox="0 0 1232 778" width="1232" height="778">
      <defs>
        <linearGradient id="gCalc" x1="0" y1="0" x2="1" y2="1">
          <stop offset="0" stop-color="#7d7d7d"/><stop offset="1" stop-color="#c9c9c9"/>
        </linearGradient>
        <radialGradient id="gPortrait" cx=".5" cy=".4" r=".6">
          <stop offset="0" stop-color="#b9b2aa"/><stop offset="1" stop-color="#5d5a57"/>
        </radialGradient>
      </defs>
      <path d="M0,0 H700 L440,778 H0 Z" fill="var(--teal-2)" opacity=".25"/>
      <path d="M880,0 H1232 V560 L1000,430 Q900,250 880,0 Z" fill="url(#gCalc)" role="img" aria-label="Photo of a calculator and financial papers"/>
      <path d="M645,560 L900,330 L1232,560 V778 H645 Z" fill="#fff"/>
      <path d="M1232,190 Q1080,175 1030,270 Q990,360 960,470 Q1100,560 1232,540 Z" fill="#2ab79f"/>
      <rect x="647" y="196" width="245" height="366" fill="var(--panel)"/>
      <path d="M1180,778 L1232,720 V778 Z" fill="var(--teal)"/>
      <circle cx="135" cy="155" r="70" fill="url(#gPortrait)" stroke="#fff" stroke-width="5" role="img" aria-label="Portrait of founder Ruth Calder"/>
      <circle cx="135" cy="155" r="78" fill="none" stroke="#fff" stroke-opacity=".25" stroke-width="6"/>
      <circle cx="383" cy="105" r="62" fill="url(#gPortrait)" stroke="#fff" stroke-width="5" role="img" aria-label="Portrait of Marcus Hale"/>
      <circle cx="383" cy="105" r="70" fill="none" stroke="#fff" stroke-opacity=".25" stroke-width="6"/>
      <circle cx="530" cy="205" r="62" fill="url(#gPortrait)" stroke="#fff" stroke-width="5" role="img" aria-label="Portrait of Lena Brooks"/>
      <circle cx="530" cy="205" r="70" fill="none" stroke="#fff" stroke-opacity=".25" stroke-width="6"/>
      <circle cx="392" cy="290" r="62" fill="url(#gPortrait)" stroke="#fff" stroke-width="5" role="img" aria-label="Portrait of Owen Pratt"/>
      <circle cx="392" cy="290" r="70" fill="none" stroke="#fff" stroke-opacity=".25" stroke-width="6"/>
      <circle cx="578" cy="145" r="7" fill="var(--panel)"/>
      <circle cx="430" cy="230" r="7" fill="var(--panel)"/>
      <circle cx="193" cy="95" r="7" fill="var(--panel)"/>
    </svg>

    <div class="abs person" style="left:460px;top:70px;width:150px"><b>Marcus Hale</b>Director of Accounting</div>
    <div class="abs person" style="left:455px;top:283px;width:150px"><b>Lena Brooks</b>Accountant</div>
    <div class="abs person light" style="left:317px;top:372px;width:150px">Accountant<b>Owen Pratt</b></div>

    <p class="abs about"><b><i>BOLR</i></b> is a professional Accounting/Bookkeeping firm located in Connecticut dedicated exclusively to Independent Insurance Agencies.</p>
    <p class="abs mission">BOLR's mission is to provide Independent Insurance Agencies a resource to have their accounting &amp; bookkeeping performed accurately, timely and cost effectively.</p>
    <div class="abs bio">
      <p>BOLR's 35 member staff is led by Ruth Calder. Ruth worked in Independent Insurance Agencies for several years before forming BOLR in 2011. Her experience includes accounting, operational management, and client service.</p>
      <p>She earned a bachelor's degree in accounting from Eastbrook State University and a master's degree in business administration from the Northfield University. Ruth is an adjunct accounting professor at Harbor Community Colleges. She serves her community as President of the local Civic Club.</p>
    </div>

    <p class="abs partner">BOLR: your partner for agency growth</p>
    <div class="abs brand-box">
      <div class="name">BOLR</div>
      <div class="full">Broker Office<br>Ledger &amp; Records</div>
      <div class="addr">&#8962; 48 Millbrook Road<br>Fairhaven, CT 06000</div>
    </div>

    <h2 class="abs premier">The premier remote bookkeeping firm for Vantrel Core agencies nationwide."</h2>

    <div class="abs services">
      <div class="service" style="top:30px">
        <svg width="48" height="48" viewBox="0 0 48 48"><circle cx="24" cy="24" r="22" fill="none" stroke="#3d4646" stroke-width="1.6"/><text x="24" y="32" text-anchor="middle" font-family="Montserrat,sans-serif" font-size="24" fill="#3d4646">$</text></svg>
        <span>Reconcile &amp;<br>Pay Agency<br>Bill Premiums</span>
      </div>
      <div class="service" style="top:97px">
        <svg width="48" height="48" viewBox="0 0 48 48"><circle cx="24" cy="24" r="22" fill="none" stroke="#3d4646" stroke-width="1.6"/><rect x="16" y="12" width="16" height="22" fill="none" stroke="#3d4646" stroke-width="1.5"/><path d="M19,18h10M19,22h10M19,26h10M19,30h7" stroke="#3d4646" stroke-width="1.3"/></svg>
        <span>Record Direct<br>Bill Commission</span>
      </div>
      <div class="service" style="top:160px">
        <svg width="48" height="48" viewBox="0 0 48 48"><circle cx="24" cy="24" r="22" fill="none" stroke="#3d4646" stroke-width="1.6"/><path d="M17,33 L19,26 L30,14 L34,18 L23,30 Z" fill="none" stroke="#3d4646" stroke-width="1.5"/></svg>
        <span>Prepare &amp;<br>Interpret Financial<br>Statements</span>
      </div>
      <div class="service" style="top:228px">
        <svg width="48" height="48" viewBox="0 0 48 48"><circle cx="24" cy="24" r="22" fill="none" stroke="#3d4646" stroke-width="1.6"/><path d="M15,34h18M17,34V18M21,34V22M25,34V16M29,34V25" stroke="#3d4646" stroke-width="2"/></svg>
        <span>Reconcile<br>General Ledger<br>Accounts</span>
      </div>
      <div class="service" style="top:298px">
        <svg width="48" height="48" viewBox="0 0 48 48"><circle cx="24" cy="24" r="22" fill="none" stroke="#3d4646" stroke-width="1.6"/><path d="M13,26h20M27,20l6,6-6,6" fill="none" stroke="#3d4646" stroke-width="1.8"/></svg>
        <span>Pay Vendor<br>Invoices</span>
      </div>
      <div class="service" style="top:370px">
        <svg width="48" height="48" viewBox="0 0 48 48"><circle cx="24" cy="24" r="22" fill="none" stroke="#3d4646" stroke-width="1.6"/><circle cx="24" cy="21" r="7" fill="none" stroke="#3d4646" stroke-width="1.5"/><path d="M21,30h6M21,33h6" stroke="#3d4646" stroke-width="1.5"/></svg>
        <span>Process Payroll</span>
      </div>
      <div class="service" style="top:430px">
        <svg width="48" height="48" viewBox="0 0 48 48"><circle cx="24" cy="24" r="22" fill="none" stroke="#3d4646" stroke-width="1.6"/><circle cx="24" cy="19" r="6" fill="none" stroke="#3d4646" stroke-width="1.5"/><path d="M13,35 Q24,22 35,35" fill="none" stroke="#3d4646" stroke-width="1.5"/></svg>
        <span>Reconcile Customer<br>Accounts Receivable</span>
      </div>
    </div>
    <p class="abs web-small">www.BrokerLedgerRecords.com</p>

    <h2 class="abs expert">Get expert assistance for Vantrel Core&reg; accounting</h2>
    <p class="abs expert-sub">The best choice for bookkeeping with Vantrel Core across the country</p>

    <div class="abs brand-back">
      <div class="name">BOLR</div>
      <div class="full">Broker Office<br>Ledger &amp; Records</div>
      <div class="web">www.BrokerLedgerRecords.com</div>
      <div class="phone">&#9990; 555.014.2290</div>
    </div>
  </section>

</main>
</body>
</html>
```